Modern & Aesthetic Electrician Sign Design for Work Vehicle

Modern and aesthetic signage design for an electricians work vehicle. Including already designed logo, mobile number, ABN, licensing number and services offered. Preference is black background, symmetric design with logo centred, services offered at bottom of sign in smaller size font. Mobile number readable and big enough to standout without being too large.

Industry/Entity Type

Electrician

Font styles to use
Serif
Sans Serif

Colors
000000
ffffff
ec1f27

Requirements
Must have
• Logo
• Services Offered
• Mobile Number
• ABN
• License Number
• Black background

```html
<!DOCTYPE html>
<html lang="en">
<head>
<meta charset="utf-8">
<title>Kestrel Electrical – Vehicle Signage</title>
<link rel="stylesheet" href="https://fonts.googleapis.com/css2?family=Exo+2:wght@200;400;600;800;900&display=swap">
<style>
  :root {
    --black: #000000;
    --white: #ffffff;
    --red: #ec1f27;
    --red-deep: #a8150f;
    --backdrop: #2b2b2b;
    --panel: #111111;
  }
  * { margin: 0; padding: 0; box-sizing: border-box; }
  html, body { width: 960px; height: 1200px; overflow: hidden; }
  body {
    background: var(--backdrop);
    font-family: "Exo 2", Arial, sans-serif;
    color: var(--white);
    position: relative;
  }
  .size-label {
    position: absolute;
    left: 0; width: 960px;
    text-align: center;
    font-weight: 200;
    font-size: 40px;
    letter-spacing: 1px;
  }
  .size-label--wide { top: 80px; }
  .size-label--compact { top: 614px; }

  .sign {
    position: absolute;
    overflow: hidden;
    background: radial-gradient(ellipse at 25% 45%, #3a3a3a 0%, #141414 45%, var(--black) 80%);
  }
  .sign--wide { left: 85px; top: 174px; width: 797px; height: 376px; }
  .sign--compact { left: 86px; top: 686px; width: 790px; height: 459px;
    background: radial-gradient(ellipse at 45% 30%, #3a3a3a 0%, #161616 50%, var(--black) 85%); }

  .sign-shapes { position: absolute; left: 0; top: 0; }

  .brand { position: absolute; text-align: center; }
  .brand-mark { border-radius: 50%; background: var(--red); margin: 0 auto; }
  .brand-name {
    font-weight: 800;
    line-height: 1;
    text-transform: uppercase;
  }
  .brand-name .line-main { display: block; }
  .brand-name .line-sub { display: block; letter-spacing: 0.55em; margin-right: -0.55em; }

  .sign--wide .brand { left: 40px; top: 90px; width: 220px; }
  .sign--wide .brand-mark { width: 90px; height: 90px; margin-bottom: 26px; }
  .sign--wide .brand-name { color: var(--red); }
  .sign--wide .brand-name .line-main { font-size: 46px; }
  .sign--wide .brand-name .line-sub { font-size: 14px; margin-top: 4px; }

  .sign--compact .brand { left: 34px; top: 40px; width: 196px; }
  .sign--compact .brand-mark { width: 90px; height: 90px; margin-bottom: 24px; }
  .sign--compact .brand-name { color: var(--white); }
  .sign--compact .brand-name .line-main { font-size: 40px; }
  .sign--compact .brand-name .line-sub { font-size: 12px; margin-top: 4px; }

  .services { position: absolute; list-style: none; }
  .services li { position: absolute; white-space: nowrap; }
  .services li::before {
    content: ""; position: absolute; border-radius: 50%; background: var(--red);
  }
  .sign--wide .services li { font-size: 13.5px; padding-left: 11px; }
  .sign--wide .services li::before { width: 4px; height: 4px; left: 0; top: 7px; }
  .sign--compact .services li { font-size: 20px; padding-left: 18px; letter-spacing: 0.5px; }
  .sign--compact .services li::before { width: 6px; height: 6px; left: 0; top: 10px; }

  .phone { position: absolute; font-weight: 900; line-height: 1; letter-spacing: 1px; }
  .sign--wide .phone { right: 23px; top: 230px; font-size: 54px; }
  .sign--compact .phone { left: 0; width: 790px; text-align: center; top: 306px; font-size: 100px; }

  .credentials { position: absolute; white-space: nowrap; line-height: 1; }
  .credentials .label { font-weight: 800; }
  .credentials .value { font-weight: 400; letter-spacing: 1px; }
  .sign--wide .credentials { right: 23px; top: 295px; font-size: 20px; }
  .sign--wide .credentials .label { color: var(--red); }
  .sign--wide .credentials .gap { display: inline-block; width: 18px; }
  .sign--compact .credentials { left: 0; width: 790px; top: 414px; font-size: 28px; display: flex; justify-content: center; align-items: center; }
  .sign--compact .credentials .divider { width: 12px; height: 12px; border-radius: 50%; background: var(--white); margin: 0 56px; }
</style>
</head>
<body>

<div class="size-label size-label--wide">1700X800</div>

<section class="sign sign--wide" aria-label="Vehicle sign, wide format">
  <svg class="sign-shapes" width="797" height="376" viewBox="0 0 797 376">
    <defs>
      <linearGradient id="band-red" x1="0" y1="0" x2="1" y2="1">
        <stop offset="0" stop-color="#c81a14"/>
        <stop offset="0.5" stop-color="#e0261a"/>
        <stop offset="1" stop-color="#8e120c"/>
      </linearGradient>
    </defs>
    <polygon points="378,0 420,0 300,376 258,376" fill="url(#band-red)" stroke="#ffffff" stroke-width="4"/>
  </svg>

  <div class="brand">
    <div class="brand-mark"></div>
    <div class="brand-name"><span class="line-main">Kestrel</span><span class="line-sub">Electrical</span></div>
  </div>

  <ul class="services">
    <li style="left:439px;top:62px">Lorem ipsum</li>
    <li style="left:439px;top:86px">Dolor sit</li>
    <li style="left:439px;top:109px">Consectetur</li>
    <li style="left:439px;top:131px">Consectetur</li>
    <li style="left:565px;top:62px">Ut enim ad</li>
    <li style="left:565px;top:86px">Duis aute</li>
    <li style="left:565px;top:109px">Laborum</li>
    <li style="left:565px;top:131px">Laborum</li>
    <li style="left:677px;top:62px">Lorem ipsum</li>
    <li style="left:677px;top:86px">Dolor sit</li>
    <li style="left:677px;top:109px">Consectetur</li>
    <li style="left:677px;top:131px">Consectetur</li>
  </ul>

  <div class="phone">123-456-789</div>
  <div class="credentials">
    <span class="label">License Number</span> <span class="value">01234</span><span class="gap"></span><span class="label">ABN</span> <span class="value">01234</span>
  </div>
</section>

<div class="size-label size-label--compact">1200X700</div>

<section class="sign sign--compact" aria-label="Vehicle sign, compact format">
  <svg class="sign-shapes" width="790" height="459" viewBox="0 0 790 459">
    <defs>
      <radialGradient id="panel-red" cx="0.5" cy="0.8" r="0.7">
        <stop offset="0" stop-color="#e2281a"/>
        <stop offset="1" stop-color="#a8150f"/>
      </radialGradient>
    </defs>
    <path d="M0,228 Q300,322 790,106 L790,459 L0,459 Z" fill="#ffffff"/>
    <path d="M0,232 Q300,338 790,124 L790,459 L0,459 Z" fill="url(#panel-red)"/>
  </svg>

  <div class="brand">
    <div class="brand-mark"></div>
    <div class="brand-name"><span class="line-main">Kestrel</span><span class="line-sub">Electrical</span></div>
  </div>

  <ul class="services">
    <li style="left:258px;top:56px">Lorem ipsum</li>
    <li style="left:258px;top:93px">Dolor sit</li>
    <li style="left:258px;top:126px">Consectetur</li>
    <li style="left:258px;top:159px">Consectetur</li>
    <li style="left:446px;top:56px">Ut enim ad</li>
    <li style="left:446px;top:93px">Duis aute</li>
    <li style="left:446px;top:126px">Laborum</li>
    <li style="left:446px;top:159px">Dolor sit</li>
    <li style="left:614px;top:56px">Lorem ipsum</li>
    <li style="left:614px;top:93px">Dolor sit</li>
  </ul>

  <div class="phone">123-456-789</div>
  <div class="credentials">
    <span><span class="label">License Number</span> <span class="value">01234</span></span>
    <span class="divider"></span>
    <span><span class="label">ABN</span> <span class="value">01234</span></span>
  </div>
</section>

</body>
</html>
```